Business Card Design for Property Development Company Director

I am looking for a professional and unforgettable business card design for our Director of our Property Development Company.
Please see attached .pptx file to find out what information to include. You don't have to follow the exact format shown in the file - I am interested to see your creative flair using the information provided.

```html
<!DOCTYPE html>
<html lang="en">
<head>
<meta charset="UTF-8">
<title>Norwell Property Group – Business Card</title>
<link href="https://fonts.googleapis.com/css2?family=Open+Sans:wght@400&family=Roboto:wght@400;700&family=Lato:wght@400&display=swap" rel="stylesheet">
<style>
  :root {
    --brand-blue: #3358a1;
    --ink-grey: #555555;
    --paper: #ffffff;
    --backdrop: #3a3a3a;
  }
  * { margin: 0; padding: 0; box-sizing: border-box; }
  html, body {
    width: 1200px;
    height: 800px;
    overflow: hidden;
    background: var(--backdrop);
  }
  .card {
    position: absolute;
    left: 316px;
    width: 570px;
    height: 330px;
    box-shadow: 0 8px 18px rgba(0,0,0,0.45);
  }
  /* Front side */
  .card--front {
    top: 51px;
    background: var(--brand-blue);
    color: var(--paper);
    font-family: "Open Sans", sans-serif;
    text-align: center;
  }
  .tagline {
    position: absolute;
    top: 50px;
    width: 100%;
    font-size: 17.5px;
    line-height: 28px;
  }
  .brand-mark {
    position: absolute;
    top: 164px;
    left: 0;
    width: 100%;
    display: flex;
    justify-content: center;
    align-items: center;
    gap: 14px;
  }
  .brand-mark__square {
    width: 36px;
    height: 36px;
    background: var(--paper);
  }
  .brand-mark__name {
    font-family: "Roboto", sans-serif;
    font-weight: 700;
    font-size: 28px;
    letter-spacing: 1px;
    text-transform: uppercase;
  }
  .offer {
    position: absolute;
    top: 274px;
    width: 100%;
    font-size: 14px;
  }
  /* Back side */
  .card--back {
    top: 418px;
    background: var(--paper);
    border-bottom: 4px solid var(--brand-blue);
    font-family: "Lato", sans-serif;
    color: var(--ink-grey);
  }
  .card--back .brand-mark {
    top: 48px;
    left: auto;
    right: 24px;
    width: auto;
    gap: 10px;
  }
  .card--back .brand-mark__square {
    width: 26px;
    height: 26px;
    background: var(--brand-blue);
  }
  .card--back .brand-mark__name {
    font-size: 19px;
    color: var(--brand-blue);
  }
  .person-name {
    position: absolute;
    left: 22px;
    top: 190px;
    font-family: "Roboto", sans-serif;
    font-weight: 700;
    font-size: 21px;
    color: var(--brand-blue);
  }
  .person-role {
    position: absolute;
    left: 22px;
    top: 218px;
    right: 24px;
    display: flex;
    align-items: center;
    gap: 7px;
    font-family: "Roboto", sans-serif;
    font-size: 16px;
  }
  .person-role::after {
    content: "";
    flex: 1;
    height: 1.5px;
    background: var(--brand-blue);
  }
  .contact-list {
    position: absolute;
    left: 22px;
    top: 249px;
    list-style: none;
    font-size: 13px;
    line-height: 20px;
  }
  .licence {
    position: absolute;
    right: 24px;
    top: 267px;
    text-align: right;
    font-size: 13px;
    line-height: 18px;
  }
</style>
</head>
<body>
  <section class="card card--front">
    <p class="tagline">Property Development &amp;<br>Site Acquisition Specialists</p>
    <div class="brand-mark">
      <span class="brand-mark__square"></span>
      <span class="brand-mark__name">Norwell Property Group</span>
    </div>
    <p class="offer">Ask me about our INVESTMENT &amp; PARTNERSHIP opportunities</p>
  </section>

  <section class="card card--back">
    <div class="brand-mark">
      <span class="brand-mark__square"></span>
      <span class="brand-mark__name">Norwell Property Group</span>
    </div>
    <h1 class="person-name">Daniel Marsh</h1>
    <p class="person-role">Director</p>
    <ul class="contact-list">
      <li>0400 123 456</li>
      <li>daniel@norwell.com.au</li>
      <li>www.norwell.com.au</li>
    </ul>
    <p class="licence">Real Estate Lic:<br>1234567 &amp; 1234568</p>
  </section>
</body>
</html>
```